K & R Acre Works. Business card design

We need a business card designed for a new business. We have a bulldozer and tractor service. We clear land and make wildlife food plots. We provide disking, bush hogging, and site prep services.
I have attached an image of a business card that I like and would like my business cards to look similar.

Target Market(s)

anyone needing bulldozer and/or tractor services

Industry/Entity Type

Business

Contact Information for Business Card

K & R Acre Works, Operated by 7-T-Ranch
Wade Colton
601-472-3358
wcr4817@fieldmail-example.com

Font styles to use
Sans Serif

Colors

Designer to choose colors to be used in the design.

Requirements
Must have
• image of tractor and bulldozer
• Land Clearing
• Wildlife food plots
• Bush Hogging
• Disking
• Site prep
Nice to have
• i have included a image of a business card that i like. I would like mine to be similar.

```html
<!DOCTYPE html>
<html lang="en">
<head>
<meta charset="utf-8">
<title>K &amp; R Acre Works – Business Card</title>
<link rel="stylesheet" href="https://fonts.googleapis.com/css2?family=Roboto+Condensed:wght@400;700&family=Roboto:wght@400;500&display=swap">
<style>
  :root {
    --page-bg: #e9e7e3;
    --photo-light: #cfcfcf;
    --photo-mid: #8a8a8a;
    --photo-dark: #3c3c3c;
    --panel-brown: rgba(120, 72, 18, 0.72);
    --accent-yellow: #e2cf2c;
    --text-white: #ffffff;
    --brand-brown: #8b5418;
    --brand-olive: #8f9a2c;
    --tagline-dark: #3a3a36;
  }
  * { box-sizing: border-box; margin: 0; padding: 0; }
  html, body {
    width: 1200px; height: 771px; overflow: hidden;
    background: var(--page-bg);
  }
  .business-card {
    position: absolute; left: 300px; top: 214px;
    width: 600px; height: 342px;
    border-radius: 14px; overflow: hidden;
    box-shadow: 0 2px 8px rgba(0,0,0,0.25);
    font-family: "Roboto", Arial, sans-serif;
  }
  .equipment-photo {
    position: absolute; inset: 0;
    background:
      linear-gradient(180deg, rgba(255,255,255,0.0) 60%, rgba(235,235,235,0.85) 100%),
      linear-gradient(100deg, var(--photo-dark) 0%, var(--photo-mid) 28%, var(--photo-light) 45%, var(--photo-mid) 70%, var(--photo-dark) 100%);
  }
  .info-panel {
    position: absolute; left: 146px; top: 55px;
    width: 454px; height: 170px;
    background: var(--panel-brown);
  }
  .owner-block { position: absolute; left: 49px; top: 33px; }
  .owner-name {
    font-family: "Roboto Condensed", Arial, sans-serif;
    font-weight: 700; font-size: 20px; color: var(--accent-yellow);
    text-transform: uppercase; letter-spacing: 0.2px; line-height: 22px;
  }
  .owner-title {
    font-family: "Roboto Condensed", Arial, sans-serif;
    font-weight: 700; font-size: 15px; color: var(--text-white);
    line-height: 20px; margin-bottom: 8px;
  }
  .contact-list { list-style: none; }
  .contact-item {
    display: flex; align-items: center; gap: 6px;
    font-size: 14px; line-height: 18px; color: var(--text-white);
  }
  .contact-icon { width: 13px; height: 13px; flex: none; }
  .services-block { position: absolute; left: 274px; top: 37px; }
  .services-heading {
    font-family: "Roboto Condensed", Arial, sans-serif;
    font-weight: 700; font-size: 18px; color: var(--accent-yellow);
    text-transform: uppercase; line-height: 20px;
  }
  .services-list { list-style: none; }
  .service-item {
    position: relative; padding-left: 11px;
    font-size: 14px; line-height: 18px; color: var(--text-white);
  }
  .service-item::before {
    content: ""; position: absolute; left: 0; top: 7px;
    width: 5px; height: 5px; border-radius: 50%;
    background: var(--accent-yellow);
  }
  .brand-line {
    position: absolute; left: 24px; top: 252px;
    display: flex; align-items: center; gap: 12px;
  }
  .brand-mark { width: 34px; height: 34px; background: var(--brand-olive); }
  .brand-name {
    font-family: "Roboto Condensed", Arial, sans-serif;
    font-weight: 700; font-size: 40px; line-height: 40px;
    color: var(--brand-brown); text-transform: uppercase; letter-spacing: 1px;
  }
  .tagline {
    position: absolute; left: 24px; right: 36px; top: 298px;
    font-family: "Roboto Condensed", Arial, sans-serif;
    font-weight: 700; font-size: 22px; line-height: 24px;
    color: var(--tagline-dark); text-transform: uppercase;
    text-align: center; letter-spacing: 0.3px;
  }
</style>
</head>
<body>
  <article class="business-card">
    <div class="equipment-photo" role="img" aria-label="Black and white photo of a bulldozer and a tractor on a cleared dirt site"></div>

    <section class="info-panel">
      <div class="owner-block">
        <h1 class="owner-name">Wade Colton</h1>
        <p class="owner-title">OWNER</p>
        <ul class="contact-list">
          <li class="contact-item">
            <svg class="contact-icon" viewBox="0 0 16 16" aria-hidden="true"><path fill="#e2cf2c" d="M3.6 1.2l2.3 2.6-1.3 1.7c.9 2 2.5 3.7 4.6 4.7l1.6-1.3 2.7 2.2-1.3 2.4C7 13 3 9 1.2 3.5z"/></svg>
            601-472-3358
          </li>
          <li class="contact-item">
            <svg class="contact-icon" viewBox="0 0 16 16" aria-hidden="true"><rect x="1" y="3" width="14" height="10" fill="#e2cf2c"/><path d="M1.5 3.5L8 9l6.5-5.5" fill="none" stroke="#7a4812" stroke-width="1.3"/></svg>
            wcr4817@fieldmail-example.com
          </li>
          <li class="contact-item">
            <svg class="contact-icon" viewBox="0 0 16 16" aria-hidden="true"><circle cx="8" cy="8" r="7" fill="#e2cf2c"/><path d="M1 8h14M8 1c-3 3.5-3 10.5 0 14M8 1c3 3.5 3 10.5 0 14" fill="none" stroke="#7a4812" stroke-width="1"/></svg>
            kracreworks-example.com
          </li>
        </ul>
      </div>

      <div class="services-block">
        <h2 class="services-heading">WE CREADED</h2>
        <ul class="services-list">
          <li class="service-item">Land Clearing</li>
          <li class="service-item">Wildlife food plots</li>
          <li class="service-item">Bush Hogging</li>
          <li class="service-item">Disking</li>
          <li class="service-item">Site prep</li>
        </ul>
      </div>
    </section>

    <div class="brand-line">
      <span class="brand-mark" aria-hidden="true"></span>
      <span class="brand-name">K &amp; R Acre Works</span>
    </div>
    <p class="tagline">For all of your land improvement needs</p>
  </article>
</body>
</html>
```